TL - business card

Tallow Partners is an insurance brokerage firm, inovative, proactive, vigorous, which aims to become the leader of the insurance brokers in Anfrica. We should like to get some designs which should be avoided also in Gray / Metallic for the Administration and Orange / Blue for the Managers (ike in the picture sent). The Blue / Green logo is not the correct one, but the source of the file. Please adjust the color accordingly for the business cards. 1 / Orange / Blue 2 / Gray / Metallic We want something classic but which is transmitted strenght, inovation, modernity and most of all, rapidity. We want something start-up like, very punchy and catching eye remaining profesional at the same time. Name: Dorian Whitlock Function: Managing Director Address: N ° 17/18 Rua Veloso - R / C 2B Direita - Bairro Mutamba - Luanda Tel: (+244) 947 582 316 Email: dorian.whitlock@tallow-p.example Website: www.tallow-p. example We want classic in the front and creative, colorfull at the back. The cards will be printed in relief, with very high quality of paper.
Insurance Broker
Colors
Designer to choose colors to be used in the design.

```html
<!DOCTYPE html>
<html lang="en">
<head>
<meta charset="utf-8">
<title>TL – Business Card</title>
<link href="https://fonts.googleapis.com/css2?family=Lato:wght@400;700;900&display=swap" rel="stylesheet">
<style>
  :root {
    --stage: #d9d9d7;
    --paper: #ffffff;
    --brand-red: #df2b28;
    --brand-orange: #f7a15e;
    --brand-blue: #0b7bc4;
    --ink: #4a4a4a;
    --accent-orange: #f08a3c;
  }
  * { margin: 0; padding: 0; box-sizing: border-box; }
  html, body { width: 1200px; height: 801px; overflow: hidden; }
  body {
    background: var(--stage);
    font-family: "Lato", sans-serif;
    position: relative;
  }
  .card {
    position: absolute;
    top: 250px;
    width: 520px;
    height: 300px;
    background: var(--paper);
    box-shadow: 0 10px 24px rgba(0,0,0,0.22);
    overflow: hidden;
  }
  .card--front { left: 45px; }
  .card--back { left: 635px; background: var(--brand-blue); }

  .front-art { position: absolute; inset: 0; }

  .holder {
    position: absolute;
    right: 34px;
    top: 24px;
    text-align: right;
    color: #fff;
  }
  .holder__name { font-weight: 900; font-size: 25px; letter-spacing: 0.5px; line-height: 1.1; }
  .holder__role { font-weight: 400; font-size: 13px; margin-top: 3px; }

  .brand {
    position: absolute;
    left: 46px;
    top: 196px;
    display: flex;
    align-items: center;
    gap: 9px;
  }
  .brand__dot {
    width: 14px; height: 14px; border-radius: 50%;
    background: var(--accent-orange);
  }
  .brand__name {
    font-weight: 900;
    font-size: 18px;
    color: var(--brand-blue);
    text-transform: uppercase;
    letter-spacing: 0.4px;
  }

  .address {
    position: absolute;
    left: 46px;
    bottom: 24px;
    color: var(--ink);
    font-size: 13px;
    line-height: 1.45;
    font-style: normal;
  }

  .contacts {
    position: absolute;
    right: 26px;
    top: 176px;
    list-style: none;
    color: var(--ink);
    font-size: 12px;
    line-height: 1.6;
    text-align: right;
  }
  .contacts li { display: flex; align-items: center; justify-content: flex-end; gap: 8px; }
  .contacts svg { width: 12px; height: 12px; flex: none; }

  .back-mark {
    position: absolute;
    right: 92px;
    top: 128px;
    display: flex;
    align-items: center;
    gap: 8px;
  }
  .back-mark__dot {
    width: 14px; height: 14px; border-radius: 50%;
    background: var(--accent-orange);
  }
  .back-mark__name {
    font-weight: 900;
    font-size: 30px;
    color: #fff;
  }
</style>
</head>
<body>

  <section class="card card--front" aria-label="Business card front">
    <svg class="front-art" viewBox="0 0 520 300" width="520" height="300" aria-hidden="true">
      <defs>
        <linearGradient id="bandGradient" x1="0" y1="1" x2="1" y2="0">
          <stop offset="0" stop-color="#df2b28"/>
          <stop offset="1" stop-color="#f7a15e"/>
        </linearGradient>
      </defs>
      <path d="M0 0 H520 V138 Q230 128 0 72 Z" fill="url(#bandGradient)"/>
      <path d="M0 82 Q230 138 520 148" fill="none" stroke="#0b7bc4" stroke-width="4"/>
    </svg>

    <div class="holder">
      <div class="holder__name">Dorian Whitlock</div>
      <div class="holder__role">Managing Director</div>
    </div>

    <div class="brand">
      <span class="brand__dot"></span>
      <span class="brand__name">Tallow Partners</span>
    </div>

    <ul class="contacts">
      <li>(+244) 947 582 316
        <svg viewBox="0 0 12 12"><circle cx="6" cy="6" r="6" fill="#0b7bc4"/><path d="M3.6 3.2c.4-.3.8-.3 1 .1l.5.9c.2.3 0 .6-.2.8l-.3.2c.3.7.8 1.2 1.5 1.5l.2-.3c.2-.2.5-.4.8-.2l.9.5c.4.2.4.6.1 1-.6.7-1.5.6-2.6-.1S3.7 5.9 3.3 4.9c-.2-.7-.1-1.3.3-1.7z" fill="#fff"/></svg>
      </li>
      <li>dorian.whitlock@tallow-p.example
        <svg viewBox="0 0 12 12"><rect x="0" y="1.5" width="12" height="9" rx="1.2" fill="#0b7bc4"/><path d="M1.5 3.2 6 6.6l4.5-3.4" fill="none" stroke="#fff" stroke-width="1.1"/></svg>
      </li>
      <li>www.tallow-p. example
        <svg viewBox="0 0 12 12"><circle cx="6" cy="6" r="6" fill="#0b7bc4"/><ellipse cx="6" cy="6" rx="2.4" ry="5" fill="none" stroke="#fff" stroke-width="0.9"/><path d="M1 6h10" stroke="#fff" stroke-width="0.9"/></svg>
      </li>
    </ul>

    <address class="address">
      N ° 17/18 Rua Veloso - R / C 2B<br>
      Direita - Bairro Mutamba - Luanda
    </address>
  </section>

  <section class="card card--back" aria-label="Business card back">
    <div class="back-mark">
      <span class="back-mark__dot"></span>
      <span class="back-mark__name">TL</span>
    </div>
  </section>

</body>
</html>
```